VKT Consulting

Government/Entitlement Consulting Services- I assist developers obtain entitlements from local, state and federal government agencies so that they can build their projects. Often these projects are very complicated and political and may face community opposition.

Target Market(s)

Real Estate Developers

Industry/Entity Type

Business Consultant

Contact Information for Business Card

Dana Melbrook
Principal

Font styles to use
Serif
Sans Serif

Requirements
Must have
• Classy and professional appeal.
Nice to have
• I like a combination of a mat and glossy finish. I've seen that done with black and then a bold color for a pop, but am not 100% committed to that.

```html
<!DOCTYPE html>
<html lang="en">
<head>
<meta charset="utf-8">
<title>VKT Consulting — Business Card</title>
<link href="https://fonts.googleapis.com/css2?family=Open+Sans:wght@400;600;700&display=swap" rel="stylesheet">
<style>
  :root {
    --backdrop: #3a3230;
    --card: #1c1c1c;
    --card-edge: #262626;
    --accent: #d9782d;
    --ink-light: #ececec;
    --ink-muted: #bdbdbd;
    --divider: #3a3a3a;
  }
  * { margin: 0; padding: 0; box-sizing: border-box; }
  html, body {
    width: 1200px; height: 900px; overflow: hidden;
    background: var(--backdrop);
    font-family: "Open Sans", Arial, sans-serif;
  }
  .stage {
    width: 1200px; height: 900px;
    display: flex; align-items: center; justify-content: center; gap: 40px;
  }
  .card {
    width: 540px; height: 309px;
    background: var(--card);
    background-image: repeating-linear-gradient(90deg, rgba(255,255,255,0.018) 0 1px, transparent 1px 3px);
    border: 1px solid var(--card-edge);
    box-shadow: 0 10px 30px rgba(0,0,0,0.45);
    position: relative;
  }

  /* Front */
  .card-front { display: flex; align-items: center; }
  .front-brand {
    width: 55%; height: 100%;
    display: flex; align-items: center; justify-content: center;
  }
  .brand-name {
    color: var(--accent);
    font-weight: 700;
    font-size: 30px;
    letter-spacing: 0.5px;
  }
  .front-divider {
    width: 1px; height: 190px; background: var(--divider);
  }
  .front-details {
    padding-left: 22px;
    color: var(--ink-light);
    font-size: 13px;
    line-height: 1.35;
  }
  .person-name { color: var(--accent); font-weight: 600; font-size: 15px; }
  .person-title { margin-bottom: 16px; }
  .address { margin-bottom: 16px; }
  .contact-list { list-style: none; }
  .contact-list li { display: flex; align-items: center; gap: 8px; }
  .contact-list svg { width: 11px; height: 11px; flex: none; }

  /* Back */
  .card-back {
    display: flex; flex-direction: column; align-items: center; justify-content: center;
    text-align: center;
  }
  .card-back .brand-name { color: var(--ink-light); font-size: 36px; }
  .tagline {
    margin-top: 36px;
    color: var(--ink-muted);
    font-size: 10.5px; font-weight: 600;
    letter-spacing: 0.3px; line-height: 1.4;
    text-transform: uppercase;
  }
</style>
</head>
<body>
<main class="stage">
  <section class="card card-front">
    <div class="front-brand">
      <span class="brand-name">VKT Consulting</span>
    </div>
    <div class="front-divider"></div>
    <div class="front-details">
      <p class="person-name">Dana Melbrook</p>
      <p class="person-title">Principal</p>
      <p class="address">12345, Address Goes Here<br>Country Name, 123456.</p>
      <ul class="contact-list">
        <li>
          <svg viewBox="0 0 12 12" aria-hidden="true"><path d="M2.5 1 L4.5 1 L5 3.5 L3.8 4.5 Q5 7 7.5 8.2 L8.5 7 L11 7.5 L11 9.5 Q11 11 9.5 11 Q1 10 1 2.5 Q1 1 2.5 1 Z" fill="var(--accent)"/></svg>
          <span>044-555 210 384</span>
        </li>
        <li>
          <svg viewBox="0 0 12 12" aria-hidden="true"><rect x="1" y="2.5" width="10" height="7" fill="var(--accent)"/><path d="M1 2.5 L6 6.5 L11 2.5" stroke="var(--card)" stroke-width="1" fill="none"/></svg>
          <span>info@vktconsult.com</span>
        </li>
        <li>
          <svg viewBox="0 0 12 12" aria-hidden="true"><circle cx="6" cy="6" r="5" fill="var(--accent)"/><path d="M1 6 H11 M6 1 Q3 6 6 11 M6 1 Q9 6 6 11" stroke="var(--card)" stroke-width="0.8" fill="none"/></svg>
          <span>www.vktconsult.com</span>
        </li>
      </ul>
    </div>
  </section>

  <section class="card card-back">
    <span class="brand-name">VKT Consulting</span>
    <p class="tagline">Government, Strategic Planning, Entitlement and<br>Public Outreach Services</p>
  </section>
</main>
</body>
</html>
```